Need to drive pregnant women to my 3d4d ultrasound studio where i provide 4d ultrasound with hyperalistic imaging and gender reveals

Industry/Entity Type

Healthcare

Font styles to use
Decorative
Script

Requirements
Must have
• My Company name Cielo de Nuestra Espera 4D. EVERYTHING HAS TO BE IN SPANISH
Nice to have
• SIMPLE AND NOT TOO BUSY
Should not have
• website

```html
<!DOCTYPE html>
<html lang="es">
<head>
<meta charset="UTF-8">
<title>Cielo de Nuestra Espera 4D</title>
<link href="https://fonts.googleapis.com/css2?family=Dancing+Script:wght@700&family=Roboto:wght@700;900&display=swap" rel="stylesheet">
<style>
  :root {
    --backdrop: #a0a0a0;
    --paper: #ffffff;
    --ink: #000000;
    --band-shine: #5c5c5e;
    --ultrasound-dark: #3a1604;
    --ultrasound-light: #c86a22;
    --newborn-dark: #9a6a5e;
    --newborn-light: #f0c8b4;
  }
  * { margin: 0; padding: 0; box-sizing: border-box; }
  html, body {
    width: 1200px;
    height: 600px;
    overflow: hidden;
    background: var(--backdrop);
    font-family: "Roboto", Arial, sans-serif;
  }
  .banner {
    position: absolute;
    left: 79px;
    top: 154px;
    width: 1042px;
    height: 304px;
    background: var(--paper);
    overflow: hidden;
    box-shadow: 0 2px 4px rgba(0, 0, 0, 0.25);
  }
  .banner__band {
    position: absolute;
    left: 0;
    top: 200px;
    width: 100%;
    height: 104px;
    background: linear-gradient(90deg, var(--ink) 0%, var(--ink) 20%, var(--band-shine) 35%, var(--ink) 62%, var(--ink) 100%);
  }
  .headline {
    position: absolute;
    left: 0;
    width: 630px;
    text-align: center;
    color: var(--ink);
    line-height: 1;
    text-transform: uppercase;
    white-space: nowrap;
  }
  .headline__top {
    top: 36px;
    font-size: 53px;
    font-weight: 700;
    letter-spacing: 0.5px;
  }
  .headline__bottom {
    top: 90px;
    font-size: 102px;
    font-weight: 900;
    letter-spacing: 1px;
  }
  .tagline {
    position: absolute;
    left: 0;
    top: 216px;
    width: 630px;
    text-align: center;
    color: var(--paper);
    font-family: "Dancing Script", "Brush Script MT", cursive;
    font-size: 30px;
    font-weight: 700;
    line-height: 36px;
    white-space: nowrap;
  }
  .gallery {
    position: absolute;
    left: 635px;
    top: 25px;
    width: 377px;
    height: 249px;
    background: var(--paper);
  }
  .gallery__photo {
    position: absolute;
    top: 4px;
    width: 183px;
    height: 241px;
  }
  .gallery__photo--scan {
    left: 4px;
    background: radial-gradient(circle at 45% 50%, var(--ultrasound-light) 0%, #8a3e10 55%, var(--ultrasound-dark) 100%);
  }
  .gallery__photo--newborn {
    left: 190px;
    background: radial-gradient(circle at 45% 55%, var(--newborn-light) 0%, #d9a691 60%, var(--newborn-dark) 100%);
  }
</style>
</head>
<body>
  <section class="banner">
    <div class="banner__band"></div>
    <h1>
      <span class="headline headline__top">Cielo de Nuestra</span>
      <span class="headline headline__bottom">Espera 4D</span>
    </h1>
    <p class="tagline">Ecografía 4D con imágenes hiperrealistas<br>y revelación de género</p>
    <div class="gallery">
      <div class="gallery__photo gallery__photo--scan" role="img" aria-label="Imagen de ecografía 4D de un bebé en tonos ámbar"></div>
      <div class="gallery__photo gallery__photo--newborn" role="img" aria-label="Fotografía de un recién nacido dormido"></div>
    </div>
  </section>
</body>
</html>
```